Heritage Hollow Business Cards

Require a business card design. <br/><br/>Needs to include logo (either round or long version) plus these details:<br/>Maya Torvell<br/>Heritage Hollow<br/>maya@kelvadtrading.com.au<br/>02 6481 7395<br/>PO Box Glenwarra NSW 2791<br/>www.heritagehollow.com.au<br/><br/>I need in an editable format so that I can create for multiple staff members. <br/><br/>

Target Market(s)

We are an online store selling renovation products to home owners are builders. Looking for a classic classy design.

Industry/Entity Type

Home And Garden

Contact Information for Business Card

Maya Torvell
Heritage Hollow
maya@kelvadtrading.com.au
02 6481 7395
PO Box Glenwarra NSW 2791
www.heritagehollow.com.au

Colors

Designer to choose colors to be used in the design.

Requirements
Must have
• Must include Logo.

```html
<!DOCTYPE html>
<html lang="en">
<head>
<meta charset="utf-8">
<title>Heritage Hollow Business Card</title>
<link rel="stylesheet" href="https://fonts.googleapis.com/css2?family=Comic+Neue:wght@700&family=Source+Sans+3:wght@400;600&display=swap">
<style>
  :root {
    --backdrop: #b0b1b4;
    --card: #0a0a0b;
    --ink: #ffffff;
    --rule: #e6e6e6;
  }
  * { margin: 0; padding: 0; box-sizing: border-box; }
  html, body { width: 1200px; height: 736px; overflow: hidden; }
  body {
    background: var(--backdrop);
    position: relative;
    font-family: "Source Sans 3", "Helvetica Neue", Arial, sans-serif;
    color: var(--ink);
  }
  .card {
    position: absolute;
    top: 142px;
    width: 444px;
    height: 444px;
    border-radius: 50%;
    background: var(--card);
  }
  .card--front { left: 132px; }
  .card--back { left: 608px; }
  .card__ring {
    position: absolute;
    left: 39px; top: 39px;
    width: 366px; height: 366px;
    border-radius: 50%;
    border: 1px solid var(--rule);
  }
  .brand {
    position: absolute;
    left: 0; right: 0;
    text-align: center;
    font-weight: 600;
    color: var(--ink);
  }
  .card--front .brand {
    top: 160px;
    font-size: 46px;
    line-height: 1.1;
  }
  .card--back .brand {
    top: 126px;
    font-size: 26px;
    line-height: 1;
  }
  .staff-name {
    position: absolute;
    left: 0; right: 0;
    top: 225px;
    text-align: center;
    font-family: "Comic Neue", "Comic Sans MS", cursive;
    font-weight: 700;
    font-size: 25px;
  }
  .staff-rule {
    position: absolute;
    left: 190px;
    top: 262px;
    width: 65px;
    height: 2px;
    background: var(--ink);
    border-radius: 1px;
  }
  .contact {
    position: absolute;
    left: 0; right: 0;
    top: 276px;
    list-style: none;
    text-align: center;
    font-size: 13px;
    line-height: 20.5px;
  }
  .contact li { display: flex; justify-content: center; align-items: center; gap: 5px; }
  .contact svg { width: 10px; height: 10px; flex: none; }
  .address {
    position: absolute;
    left: 0; right: 0;
    top: 349px;
    text-align: center;
    font-size: 13px;
    line-height: 18px;
  }
</style>
</head>
<body>
  <section class="card card--front" aria-label="Card front">
    <div class="card__ring"></div>
    <p class="brand">Heritage<br>Hollow</p>
  </section>

  <section class="card card--back" aria-label="Card back">
    <div class="card__ring"></div>
    <p class="brand">Heritage Hollow</p>
    <h1 class="staff-name">Maya Torvell</h1>
    <div class="staff-rule"></div>
    <ul class="contact">
      <li>
        <svg viewBox="0 0 10 10" aria-hidden="true"><path d="M2 0.8 L3.6 2.8 L2.8 3.8 C3.4 5 4.8 6.5 6.2 7.2 L7.2 6.4 L9.2 8 L8 9.4 C4.5 9 1 5.5 0.6 2 Z" fill="#fff"/></svg>
        <span>02 6481 7395</span>
      </li>
      <li>
        <svg viewBox="0 0 10 10" aria-hidden="true"><rect x="0.5" y="2" width="9" height="6.5" fill="#fff"/><path d="M0.5 2 L5 5.8 L9.5 2" fill="none" stroke="#0a0a0b" stroke-width="0.9"/></svg>
        <span>maya@kelvadtrading.com.au</span>
      </li>
      <li>
        <svg viewBox="0 0 10 10" aria-hidden="true"><g fill="none" stroke="#fff" stroke-width="0.8"><circle cx="5" cy="5" r="4.4"/><ellipse cx="5" cy="5" rx="2" ry="4.4"/><path d="M0.6 5 H9.4 M1.3 2.8 H8.7 M1.3 7.2 H8.7"/></g></svg>
        <span>www.heritagehollow.com.au</span>
      </li>
    </ul>
    <p class="address">PO Box Glenwarra<br>NSW 2791</p>
  </section>
</body>
</html>
```